BOLD & MINIMALIST DESIGN NEEDED

We want a very bold but minimalistic business card design that is impactful and utilizes both sides of the business card. Our current logo is included for your use.

We want bold fonts and good use of negative space. We don't want the logo to overpower the design.

Target Market(s)

Professionals who are building new commercial buildings.

Industry/Entity Type

Construction

Contact Information for Business Card

Name, Title, email, office phone, cell phone, website

Font styles to use
Serif
Sans Serif

Requirements
Must have
• Bold design!

```html
<!DOCTYPE html>
<html lang="en">
<head>
<meta charset="utf-8">
<title>Ridgeline Build – Business Card</title>
<link href="https://fonts.googleapis.com/css2?family=Montserrat:wght@400;500;700;800&display=swap" rel="stylesheet">
<style>
  :root{
    --bg:#3a3a3a;
    --card:#1e1e1e;
    --ink:#ffffff;
    --muted:#d9d9d9;
    --green:#7dc242;
    --front-mark:#2e2e2e;
  }
  *{box-sizing:border-box;margin:0;padding:0}
  html,body{width:1200px;height:875px;overflow:hidden}
  body{
    background:var(--bg);
    font-family:"Montserrat",sans-serif;
    display:flex;align-items:center;justify-content:center;gap:40px;
  }
  .card{
    position:relative;width:540px;height:309px;
    background:var(--card);border-radius:16px;overflow:hidden;
    box-shadow:0 14px 30px rgba(0,0,0,.45);
  }
  .wordmark{
    display:flex;align-items:center;gap:10px;
    font-family:"Montserrat",sans-serif;font-weight:800;
    letter-spacing:1px;line-height:1;white-space:nowrap;
  }
  .wordmark .dot{width:12px;height:12px;border-radius:50%;background:var(--green);flex:none}
  .card-front .wordmark{
    position:absolute;left:50%;top:50%;transform:translate(-50%,-50%);
    color:var(--front-mark);font-size:34px;
  }
  .card-front .wordmark .dot{width:16px;height:16px;background:var(--front-mark)}
  .card-back .wordmark{
    position:absolute;left:30px;top:150px;color:var(--ink);font-size:19px;
  }
  .divider{
    position:absolute;left:286px;top:60px;width:1px;height:170px;
    background:var(--green);opacity:.7;
  }
  .contact{position:absolute;left:306px;top:62px;color:var(--ink)}
  .contact .name{
    color:var(--green);font-weight:700;font-size:20px;letter-spacing:.5px;
  }
  .contact .title{font-size:12px;font-weight:500;margin-top:2px;margin-bottom:20px}
  .contact ul{list-style:none}
  .contact li{
    display:flex;align-items:center;gap:8px;white-space:nowrap;
    font-size:12px;font-weight:500;margin-bottom:7px;color:var(--muted);
  }
  .contact li svg{width:11px;height:11px;fill:var(--green);flex:none}
  .contact .domain{color:var(--green)}
  .bands{position:absolute;left:0;bottom:0;width:540px;height:309px;pointer-events:none}
</style>
</head>
<body>

  <section class="card card-front" aria-label="Card front">
    <div class="wordmark"><span class="dot"></span><span>RIDGELINE BUILD</span></div>
  </section>

  <section class="card card-back" aria-label="Card back">
    <div class="wordmark"><span class="dot"></span><span>RIDGELINE BUILD</span></div>
    <div class="divider"></div>
    <div class="contact">
      <p class="name">DALTON REEVE</p>
      <p class="title">Owner/CEO</p>
      <ul>
        <li><svg viewBox="0 0 24 24"><path d="M6.6 10.8a15 15 0 0 0 6.6 6.6l2.2-2.2c.3-.3.7-.4 1-.2 1.1.4 2.3.6 3.6.6.6 0 1 .4 1 1V20c0 .6-.4 1-1 1A17 17 0 0 1 3 4c0-.6.4-1 1-1h3.5c.6 0 1 .4 1 1 0 1.3.2 2.5.6 3.6.1.3 0 .7-.2 1z"/></svg><span>07 5123 4400</span></li>
        <li><svg viewBox="0 0 24 24"><path d="M7 1h10a2 2 0 0 1 2 2v18a2 2 0 0 1-2 2H7a2 2 0 0 1-2-2V3a2 2 0 0 1 2-2zm0 3v14h10V4z"/></svg><span>0412 555 019</span></li>
        <li><svg viewBox="0 0 24 24"><path d="M2 5h20v14H2zm2 2v.5l8 5 8-5V7z"/></svg><span>info@ridgelinebuild.com</span></li>
        <li><svg viewBox="0 0 24 24"><path d="M12 2a10 10 0 1 0 0 20 10 10 0 0 0 0-20zm0 2c1.2 1.5 2 3.6 2.2 6H9.8C10 7.6 10.8 5.5 12 4zM4.1 13h3.7c.1 2.4.8 4.5 1.9 6A8 8 0 0 1 4.1 13zm0-2a8 8 0 0 1 5.6-6c-1.1 1.5-1.8 3.6-1.9 6zm5.7 2h4.4c-.2 2.4-1 4.5-2.2 6-1.2-1.5-2-3.6-2.2-6zm4.5 6c1.1-1.5 1.8-3.6 1.9-6h3.7a8 8 0 0 1-5.6 6zm1.9-8c-.1-2.4-.8-4.5-1.9-6a8 8 0 0 1 5.6 6z"/></svg><span>www.<span class="domain">ridgelinebuild</span>.com</span></li>
      </ul>
    </div>
    <svg class="bands" viewBox="0 0 540 309" aria-hidden="true">
      <polygon points="0,298 392,280 384,309 0,309" fill="var(--green)"/>
      <polygon points="404,279 540,228 540,252 412,296 400,309 392,309" fill="var(--ink)"/>
    </svg>
  </section>

</body>
</html>
```